Mushroom Focus Gummies

I need a poster 12inches W X 17 inches H advertising my functional mushroom company, Quillbright. My website is quillbright.life "Have you ever walked into a room and forgot what you are doing? Lions Mane can help with that." At Quillbright, we put the Fun in Functional mushrooms. Its needs to be informative and fun. I need our three producst advertised here. Our Focus gummy, great natural alternative to prentizol, or any one looking to improve focus and memory. They taste amazing with Its blue berry clarity flavoring. Our Moravel is a great natural sleep aid. No melotonin or heavy sedatitives. Our Ola-Vex gummy is a longevity combination of the top five functional mushrooms.
Ive attached an example of our old poster.
Anyone looking for an alternative to prentizoll or wanting to improve memory and focus
Mushroom

```html
<!DOCTYPE html>
<html lang="en">
<head>
<meta charset="UTF-8">
<title>Quillbright – Functional Mushrooms Poster</title>
<link href="https://fonts.googleapis.com/css2?family=Poppins:wght@400;600;700;800&display=swap" rel="stylesheet">
<style>
  :root {
    --page-bg: #c4c6c5;
    --violet-deep: #2a0c96;
    --violet: #45079c;
    --magenta-glow: #7a0a98;
    --mint: #6fe3d3;
    --mint-soft: #a6ece2;
    --pink: #ff1a9a;
    --lavender: #9a97b8;
    --white: #ffffff;
    --ink: #141414;
  }
  * { box-sizing: border-box; margin: 0; padding: 0; }
  html, body { width: 981px; height: 1200px; overflow: hidden; }
  body {
    background: var(--page-bg);
    font-family: "Poppins", sans-serif;
    display: flex;
    justify-content: center;
  }
  .poster {
    position: relative;
    width: 848px;
    height: 1200px;
    overflow: hidden;
    background:
      radial-gradient(ellipse 420px 520px at 40px 420px, var(--magenta-glow) 0%, rgba(122,10,152,0) 100%),
      linear-gradient(180deg, var(--violet-deep) 0%, var(--violet) 60%, #55108e 100%);
    color: var(--white);
  }
  .brand { position: absolute; top: 96px; left: 0; width: 100%; text-align: center; }
  .brand-name {
    font-size: 62px; font-weight: 600; color: var(--mint);
    letter-spacing: 1px; line-height: 1;
  }
  .brand-tagline {
    margin-top: 10px; margin-left: 200px;
    font-size: 15px; font-weight: 600; letter-spacing: 4px;
  }
  .headline { position: absolute; top: 222px; left: 0; width: 100%; text-align: center; }
  .headline-lead { font-size: 54px; font-weight: 600; color: var(--mint); line-height: 1.1; letter-spacing: 0.5px; }
  .headline-main {
    font-size: 100px; font-weight: 800; line-height: 0.88; letter-spacing: 2px;
    margin-top: 8px;
  }
  .question {
    position: absolute; top: 482px; left: 0; width: 100%; text-align: center;
    font-size: 35px; font-weight: 700; color: var(--mint); line-height: 1.12; letter-spacing: 0.5px;
  }
  .answer {
    position: absolute; top: 569px; left: 0; width: 100%; text-align: center;
    font-size: 27px; font-weight: 600;
  }
  .product-card {
    position: absolute; top: 655px; width: 216px; height: 170px;
    background: var(--white); border-radius: 30px 30px 0 0;
    color: var(--ink); text-align: center;
    font-size: 14.5px; line-height: 1.22; padding: 48px 14px 0;
  }
  .product-tab {
    position: absolute; top: -23px; left: 29px; width: 158px; height: 55px;
    border-radius: 10px; border: 2px solid #3a0a8a;
    display: flex; align-items: center; justify-content: center;
    font-weight: 700; font-size: 22px; line-height: 0.95;
  }
  .card-olavex { left: 76px; }
  .card-focus { left: 324px; }
  .card-moravel { left: 570px; }
  .tab-olavex { background: var(--mint-soft); color: var(--ink); }
  .tab-focus { background: var(--pink); color: var(--white); font-size: 24px; }
  .tab-moravel { background: var(--lavender); color: var(--white); }
  .table-surface {
    position: absolute; left: 0; bottom: 0; width: 100%; height: 187px;
    background: linear-gradient(180deg, #6e4a86 0%, #5a3a6c 40%, #3e2748 100%);
  }
  .jar { position: absolute; top: 805px; height: 292px; border-radius: 40px 40px 36px 36px; }
  .jar-olavex { left: 57px; width: 245px; background: linear-gradient(180deg, #8fe6d8 0%, #5cc0ac 36%, #0b0b0b 37%, #111 100%); }
  .jar-focus { left: 296px; width: 254px; background: linear-gradient(180deg, #f49ad0 0%, #d9509a 38%, #2a3556 39%, #303c5e 100%); }
  .jar-moravel { left: 547px; width: 262px; background: linear-gradient(180deg, #cfcdee 0%, #8e8cb6 37%, #2a2426 38%, #332b2d 100%); }
  .follow {
    position: absolute; left: 52px; top: 1122px;
    display: flex; align-items: center; gap: 14px;
    font-size: 21px; font-weight: 600; color: var(--pink);
  }
  .social-dot { width: 20px; height: 20px; border-radius: 50%; background: var(--white); }
  .web-bar {
    position: absolute; left: 390px; top: 1120px; width: 458px; height: 35px;
    background: var(--pink); border-radius: 18px 0 0 18px;
    display: flex; align-items: center; padding-left: 24px; gap: 8px;
    font-size: 25px; font-weight: 600; letter-spacing: 1.5px;
  }
  .web-bar svg { flex: none; }
</style>
</head>
<body>
  <main class="poster">
    <header class="brand">
      <div class="brand-name">Quillbright</div>
      <div class="brand-tagline">BRIGHTEN EVERY DAY</div>
    </header>

    <section class="headline">
      <p class="headline-lead">We put the fun in</p>
      <h1 class="headline-main">FUNCTIONAL<br>MUSHROOMS</h1>
    </section>

    <p class="question">Have you ever walked into a room<br>&amp; forgot what you are doing?</p>
    <p class="answer">Functional Mushrooms can help with that.</p>

    <div class="table-surface" role="img" aria-label="Wooden tabletop the product jars stand on"></div>

    <article class="product-card card-olavex">
      <div class="product-tab tab-olavex">Ola-Vex</div>
      is a blend of the top 5 functional mushrooms. Great for mushroom enthusaist looking to supplement with them.
    </article>
    <article class="product-card card-focus">
      <div class="product-tab tab-focus">Focus<br>Gummies</div>
      A great natural alternative to prentizol, or anyone looking to improve memory and focus.
    </article>
    <article class="product-card card-moravel">
      <div class="product-tab tab-moravel">Moravel</div>
      Amazing blend of functional mushrooms and natural sleep aids for anyone looking to improve deep sleep.
    </article>

    <div class="jar jar-olavex" role="img" aria-label="Ola-Vex mushroom gummies jar, mint lid, Citrus Evergreen flavour"></div>
    <div class="jar jar-focus" role="img" aria-label="Focus mushroom gummies jar, pink lid, Berry Sharp flavour"></div>
    <div class="jar jar-moravel" role="img" aria-label="Moravel mushroom gummies jar, lavender lid, Dusk Honeydew flavour"></div>

    <footer>
      <div class="follow">
        <span>Follow us on</span>
        <span class="social-dot"></span>
        <span class="social-dot"></span>
        <span class="social-dot"></span>
        <span class="social-dot"></span>
      </div>
      <div class="web-bar">
        <svg width="16" height="16" viewBox="0 0 16 16" aria-hidden="true">
          <circle cx="8" cy="8" r="6.5" fill="none" stroke="#fff" stroke-width="1.6"/>
          <ellipse cx="8" cy="8" rx="2.8" ry="6.5" fill="none" stroke="#fff" stroke-width="1.3"/>
          <line x1="1.5" y1="8" x2="14.5" y2="8" stroke="#fff" stroke-width="1.3"/>
        </svg>
        <span>www.quillbright.life.com</span>
      </div>
    </footer>
  </main>
</body>
</html>
```